Brightmill Data Works

Our company is about IT hardwares and IT solutions. IT hardware such as PC, RAMS, storage and servers. IT solutions such as project management, BA. We are also selling new technology too.

Target Market(s)

Consumer, Small to Medium Business, Corporate

Requirements
Must have
• The business card must have the following:
• Name:
• Title:
• Contact Number:
• Email address:
• Website:
• Color: Must match the logo color upgrade

```html
<!DOCTYPE html>
<html lang="en">
<head>
<meta charset="utf-8">
<title>Brightmill Data Works – Business Card</title>
<link rel="stylesheet" href="https://fonts.googleapis.com/css2?family=Saira:wght@700&family=Roboto:wght@400;500&display=swap">
<style>
  :root {
    --stage: #2b2b2b;
    --card-light: #f1f1f1;
    --card-dark: #1f1f1f;
    --ink-grey: #4f4f4f;
    --ink-white: #f3f3f3;
    --accent: #d9923a;
    --text-light: #e6e6e6;
  }
  * { box-sizing: border-box; margin: 0; padding: 0; }
  html, body {
    width: 1200px;
    height: 997px;
    overflow: hidden;
    background: var(--stage);
  }
  .canvas {
    position: relative;
    width: 1200px;
    height: 997px;
  }
  .card {
    position: absolute;
    left: 290px;
    width: 620px;
    height: 354px;
    border-radius: 18px;
    overflow: hidden;
  }
  .card--front {
    top: 120px;
    background: var(--card-light);
    display: flex;
    align-items: center;
    justify-content: center;
  }
  .card--back {
    top: 524px;
    background: var(--card-dark);
  }
  .wordmark {
    font-family: "Saira", "Arial Black", sans-serif;
    font-weight: 700;
    text-transform: uppercase;
    line-height: 1.02;
    letter-spacing: 1px;
  }
  .card--front .wordmark {
    display: flex;
    align-items: center;
    gap: 22px;
    color: var(--ink-grey);
    font-size: 46px;
  }
  .wordmark__square {
    width: 58px;
    height: 58px;
    background: var(--accent);
    flex: none;
  }
  .card--back .wordmark {
    position: absolute;
    top: 52px;
    left: 170px;
    color: var(--ink-white);
    font-size: 34px;
  }
  .divider {
    position: absolute;
    left: 222px;
    right: 40px;
    top: 214px;
    height: 2px;
    background: var(--accent);
  }
  .person {
    position: absolute;
    left: 42px;
    top: 190px;
    font-family: "Roboto", Arial, sans-serif;
  }
  .person__name {
    color: var(--accent);
    font-weight: 500;
    font-size: 20px;
    letter-spacing: 0.5px;
    text-transform: uppercase;
  }
  .person__title {
    color: var(--text-light);
    font-size: 17px;
    margin-top: 2px;
  }
  .website {
    position: absolute;
    right: 40px;
    top: 228px;
    font-family: "Roboto", Arial, sans-serif;
    color: var(--accent);
    font-size: 16px;
    letter-spacing: 1.5px;
  }
  .contacts {
    position: absolute;
    left: 42px;
    top: 260px;
    list-style: none;
    font-family: "Roboto", Arial, sans-serif;
    color: var(--text-light);
    font-size: 17px;
  }
  .contacts__item {
    display: flex;
    align-items: center;
    gap: 12px;
    height: 26px;
  }
  .contacts__icon {
    width: 16px;
    height: 16px;
    flex: none;
  }
</style>
</head>
<body>
<main class="canvas">
  <section class="card card--front" aria-label="Card front">
    <div class="wordmark">
      <span class="wordmark__square" aria-hidden="true"></span>
      <span>Brightmill<br>Data Works</span>
    </div>
  </section>

  <section class="card card--back" aria-label="Card back">
    <div class="wordmark">Brightmill Data Works</div>
    <div class="divider" aria-hidden="true"></div>

    <div class="person">
      <p class="person__name">Dana Corliss</p>
      <p class="person__title">Director</p>
    </div>

    <p class="website">www.brightmilldata.com</p>

    <ul class="contacts">
      <li class="contacts__item">
        <svg class="contacts__icon" viewBox="0 0 16 16" aria-hidden="true">
          <circle cx="8" cy="8" r="8" fill="#d9923a"/>
          <path d="M5 4.5h2l.6 2-1 .8a5 5 0 0 0 2.1 2.1l.8-1 2 .6v2c-4 .4-7-2.6-6.5-6.5z" fill="#1f1f1f"/>
        </svg>
        <span>555.013.2741</span>
      </li>
      <li class="contacts__item">
        <svg class="contacts__icon" viewBox="0 0 16 16" aria-hidden="true">
          <circle cx="8" cy="8" r="8" fill="#d9923a"/>
          <rect x="4" y="5.5" width="8" height="5" rx="1" fill="#1f1f1f"/>
          <rect x="6" y="4" width="4" height="1.5" fill="#1f1f1f"/>
        </svg>
        <span>555.019.6630</span>
      </li>
      <li class="contacts__item">
        <svg class="contacts__icon" viewBox="0 0 16 16" aria-hidden="true">
          <circle cx="8" cy="8" r="8" fill="#d9923a"/>
          <rect x="4" y="5" width="8" height="6" fill="#1f1f1f"/>
          <path d="M4 5l4 3.2L12 5" stroke="#d9923a" stroke-width="1" fill="none"/>
        </svg>
        <span>dana@brightmilldata.com</span>
      </li>
    </ul>
  </section>
</main>
</body>
</html>
```